Flyer-Design für Shop für nachhaltige Haustierprodukte
LOMERU
Tolle Umsetzung nach den Vorgaben. Änderungen super und schnell umgesetzt. Gerne wieder!
Zielgruppe
LOMERU ist ein Online-Marktplatz für nachhaltige Haustierprodukte. Meine Zielgruppe sind Frauen zwischen 30 und 60 Jahren mit Haustieren (Hund, Katze, Pferd)
Aufgabenstellung
Das Design soll an der Webseite angepasst sein. Es ist wichtig, dass das Thema Nachhaltigkeit kommuniziert wird und welche Vorteile LOMERU hat (Markenvielvalt, kleine Manufakturen, Handmade etc.)

```html
<!DOCTYPE html>
<html lang="de">
<head>
<meta charset="utf-8">
<title>LOMERU Flyer</title>
<link rel="stylesheet" href="https://fonts.googleapis.com/css2?family=Montserrat:wght@400;500;600;700&display=swap">
<style>
  :root {
    --paper: #f3f2ec;
    --white: #ffffff;
    --brand-orange: #f26d0c;
    --accent-orange: #ee7a33;
    --band-orange: #ee7732;
    --ink: #111111;
    --photo-green-light: #7aa64a;
    --photo-green-dark: #4f7a2e;
    --photo-olive: #7d8552;
  }
  html, body {
    margin: 0;
    padding: 0;
    width: 1200px;
    height: 2400px;
    overflow: hidden;
    background: var(--paper);
  }
  .flyer {
    position: relative;
    width: 1200px;
    height: 2400px;
    background: var(--paper);
    font-family: "Montserrat", sans-serif;
    color: var(--ink);
    overflow: hidden;
  }
  .hero-photo {
    position: absolute;
    left: 0; top: 0;
    width: 1200px; height: 748px;
    background: linear-gradient(180deg, var(--photo-green-light) 0%, var(--photo-green-dark) 55%, var(--photo-olive) 100%);
  }
  .brand-box {
    position: absolute;
    left: 122px; top: 661px;
    width: 950px; height: 237px;
    background: var(--white);
    border-radius: 42px;
  }
  .brand-mark {
    position: absolute;
    left: 77px; top: 53px;
  }
  .brand-name {
    position: absolute;
    left: 226px; top: 38px;
    font-weight: 500;
    font-size: 155px;
    line-height: 160px;
    letter-spacing: 0;
    color: var(--brand-orange);
  }
  .kicker {
    position: absolute;
    left: 121px; top: 1018px;
    margin: 0;
    font-weight: 500;
    font-size: 43px;
    line-height: 54px;
    color: var(--ink);
  }
  .headline {
    position: absolute;
    left: 119px; top: 1086px;
    margin: 0;
    font-weight: 700;
    font-size: 89px;
    line-height: 102px;
    color: var(--accent-orange);
  }
  .animal-icons {
    position: absolute;
    left: 120px; top: 1447px;
    display: flex;
    gap: 44px;
  }
  .benefits {
    position: absolute;
    left: 122px; top: 1678px;
    margin: 0; padding: 0;
    list-style: none;
  }
  .benefits li {
    display: flex;
    align-items: center;
    height: 81px;
    font-weight: 500;
    font-size: 43px;
  }
  .benefits svg { margin-right: 43px; flex: none; }
  .footer-band {
    position: absolute;
    left: 0; top: 2219px;
    width: 1200px; height: 181px;
    background: var(--band-orange);
    display: flex;
    align-items: center;
    justify-content: center;
  }
  .web-address {
    color: var(--white);
    font-weight: 700;
    font-size: 56px;
  }
</style>
</head>
<body>
<div class="flyer">
  <div class="hero-photo" role="img" aria-label="Foto: Hund liegt im Gras und kaut an einem Kauknochen"></div>

  <div class="brand-box">
    <svg class="brand-mark" width="128" height="128" viewBox="0 0 128 128" aria-hidden="true">
      <circle cx="64" cy="64" r="60" fill="none" stroke="var(--brand-orange)" stroke-width="5"/>
    </svg>
    <span class="brand-name">LOMERU</span>
  </div>

  <p class="kicker">NACHHALTIG LEBEN MIT HAUSTIEREN</p>
  <h1 class="headline">Online-Marktplatz<br>für nachhaltige<br>Tierprodukte</h1>

  <div class="animal-icons">
    <svg width="140" height="140" viewBox="0 0 140 140" role="img" aria-label="Symbol Hund"><circle cx="70" cy="70" r="67" fill="none" stroke="var(--accent-orange)" stroke-width="4"/></svg>
    <svg width="140" height="140" viewBox="0 0 140 140" role="img" aria-label="Symbol Katze"><circle cx="70" cy="70" r="67" fill="none" stroke="var(--accent-orange)" stroke-width="4"/></svg>
    <svg width="140" height="140" viewBox="0 0 140 140" role="img" aria-label="Symbol Pferd"><circle cx="70" cy="70" r="67" fill="none" stroke="var(--accent-orange)" stroke-width="4"/></svg>
  </div>

  <ul class="benefits">
    <li><svg width="54" height="50" viewBox="0 0 54 50" aria-hidden="true"><path d="M40 14 A21 21 0 1 0 44 30" fill="none" stroke="var(--ink)" stroke-width="4" stroke-linecap="round"/><path d="M14 24 L24 34 L48 6" fill="none" stroke="var(--ink)" stroke-width="4" stroke-linecap="round" stroke-linejoin="round"/></svg>Marktplatz mit großer Produktauswahl</li>
    <li><svg width="54" height="50" viewBox="0 0 54 50" aria-hidden="true"><path d="M40 14 A21 21 0 1 0 44 30" fill="none" stroke="var(--ink)" stroke-width="4" stroke-linecap="round"/><path d="M14 24 L24 34 L48 6" fill="none" stroke="var(--ink)" stroke-width="4" stroke-linecap="round" stroke-linejoin="round"/></svg>Nachhaltiges Futtermittel</li>
    <li><svg width="54" height="50" viewBox="0 0 54 50" aria-hidden="true"><path d="M40 14 A21 21 0 1 0 44 30" fill="none" stroke="var(--ink)" stroke-width="4" stroke-linecap="round"/><path d="M14 24 L24 34 L48 6" fill="none" stroke="var(--ink)" stroke-width="4" stroke-linecap="round" stroke-linejoin="round"/></svg>Handgefertigte Accesoires</li>
    <li><svg width="54" height="50" viewBox="0 0 54 50" aria-hidden="true"><path d="M40 14 A21 21 0 1 0 44 30" fill="none" stroke="var(--ink)" stroke-width="4" stroke-linecap="round"/><path d="M14 24 L24 34 L48 6" fill="none" stroke="var(--ink)" stroke-width="4" stroke-linecap="round" stroke-linejoin="round"/></svg>Originelles Spielzeug u.v.m.</li>
    <li><svg width="54" height="50" viewBox="0 0 54 50" aria-hidden="true"><path d="M40 14 A21 21 0 1 0 44 30" fill="none" stroke="var(--ink)" stroke-width="4" stroke-linecap="round"/><path d="M14 24 L24 34 L48 6" fill="none" stroke="var(--ink)" stroke-width="4" stroke-linecap="round" stroke-linejoin="round"/></svg>Für Hunde, Katzen und Pferde</li>
  </ul>

  <div class="footer-band">
    <span class="web-address">www.lomeru.de</span>
  </div>
</div>
</body>
</html>
```